Vindgerdi - Start-up company selling electricity

Hello let me tell you about Vindgerdi.

Vindgerdi is start-up company selling electricity in Iceland. The operations of the company consist of making power usage forecasts for our customers, purchasing the electricity wholesale from the energy producers, and selling the electricity to the consumer. We are focused on tech by using optimization and machine learning to minimize electricity prices to our customers. Our marketing strategy is to portray a tech company mindset and to show dedication to driving down the electricity price on the market.

We need your help to make our website pop. Possible concepts to work with are as follows:

- Iceland the land of ice and fire
- Green energy
- Innovation
- Tech and data science

Link to our website: https://prufa.vindgerdi-example.is/
We are open to ideas.
Thank you!

Target Market(s)

Electricity consumers both homes and companies.

Number of Pages Required

1 page

Font styles to use
Serif
Sans Serif

```html
<!DOCTYPE html>
<html lang="is">
<head>
<meta charset="utf-8">
<title>Vindgerdi</title>
<link href="https://fonts.googleapis.com/css2?family=Aldrich&family=Cinzel:wght@500;700&family=Mulish:wght@400&display=swap" rel="stylesheet">
<style>
:root{
  --green:#7c9a02;
  --orange:#f65b05;
  --dark:#333333;
  --text:#1f1f1f;
  --white:#ffffff;
  --card-border:#ececec;
}
*{box-sizing:border-box;margin:0;padding:0}
html,body{width:1200px;height:1129px;overflow:hidden;background:var(--white)}
body{position:relative;font-family:'Mulish',sans-serif;color:var(--text)}
.hero{position:absolute;left:0;top:0;width:1200px;height:392px;overflow:hidden}
.hero-photo{position:absolute;inset:0;background:linear-gradient(180deg,#1657b0 0%,#2f7cc4 30%,#a9c3b0 52%,#f0c130 70%,#e7a114 82%,#b67a1c 100%)}
.hero-wave{position:absolute;left:0;bottom:0;width:1200px;height:80px}
.brand{position:absolute;left:141px;top:30px;height:46px;display:flex;align-items:center;gap:12px}
.brand-dot{width:30px;height:30px;border-radius:50%;background:var(--white)}
.brand-name{font-family:'Cinzel',serif;font-weight:700;font-size:36px;line-height:46px;color:var(--white);letter-spacing:.5px}
.nav a{position:absolute;top:52px;font-family:'Aldrich',sans-serif;font-size:13.5px;line-height:18px;color:var(--white);text-decoration:none;white-space:nowrap}
.nav .n1{left:625px}
.nav .n2{left:805px}
.nav .n3{left:952px}
.headline{position:absolute;left:141px;top:135px;font-family:'Aldrich',sans-serif;font-weight:400;font-size:37px;line-height:55px;color:var(--white);text-shadow:2px 3px 4px rgba(0,0,0,.45)}
.cards{position:absolute;top:440px;left:141px;display:flex;gap:18px}
.card{width:294px;height:387px;border:1px solid var(--card-border);box-shadow:0 0 6px rgba(0,0,0,.05);text-align:center;position:relative}
.icon-ring{width:122px;height:122px;margin:29px auto 0;border-radius:50%;border:1px solid #dcdcdc;display:flex;align-items:center;justify-content:center}
.icon-disc{width:110px;height:110px;border-radius:50%;background:radial-gradient(circle at 50% 40%,#fff 0%,#ececec 100%);display:flex;align-items:center;justify-content:center}
.card-title{font-family:'Aldrich',sans-serif;font-weight:400;font-size:14.5px;line-height:20px;margin-top:16px}
.card-text{font-size:13px;line-height:19px;margin:10px 27px 0}
.btns{position:absolute;left:0;right:0;bottom:24px;display:flex;justify-content:center;gap:7px}
.btn{width:113px;height:39px;display:flex;align-items:center;justify-content:center;font-family:'Cinzel',serif;font-weight:500;font-size:13px;letter-spacing:1px;color:var(--white);background:var(--green);text-decoration:none}
.btn.alt{background:var(--orange)}
.prices{display:flex;margin-top:12px;height:78px}
.price{flex:1;font-size:12.5px;line-height:16px}
.price + .price{border-left:1px solid #ddd}
.price b{display:block;font-family:Arial,sans-serif;font-weight:400;font-size:20px;line-height:30px;margin-bottom:1px}
.compare{font-size:12.5px;line-height:16px;margin-top:11px}
.footer{position:absolute;left:0;top:902px;width:1200px;height:190px;background:var(--dark);color:var(--white)}
.contact{position:absolute;display:flex;gap:14px;align-items:flex-start}
.contact-icon{width:43px;height:43px;border-radius:50%;background:var(--green);border:2px solid #fff;display:flex;align-items:center;justify-content:center;flex:none}
.contact-text{font-size:14px;line-height:21px}
.contact-head{font-family:'Cinzel',serif;font-size:15px;letter-spacing:1px;line-height:20px;margin-bottom:3px}
.footer-mark{position:absolute;left:570px;top:46px;width:60px;height:60px;border-radius:50%;background:var(--green)}
.company{position:absolute;left:0;right:0;top:134px;text-align:center;font-family:'Cinzel',serif;font-size:13px;letter-spacing:1px;line-height:19px}
.copyright{position:absolute;left:0;top:1092px;width:1200px;height:37px;background:var(--green);color:var(--white);font-size:12.5px;display:flex;align-items:center;justify-content:center}
</style>
</head>
<body>
<header class="hero">
  <div class="hero-photo" role="img" aria-label="Photograph of power transmission pylons against a sunset sky, blue above fading to yellow and orange"></div>
  <svg class="hero-wave" viewBox="0 0 1200 80" preserveAspectRatio="none">
    <path d="M0 20 C150 60 300 70 450 62 C650 50 800 20 950 18 C1080 16 1150 40 1200 66 L1200 80 L0 80 Z" fill="#fff"/>
    <path d="M0 20 C150 60 300 70 450 62 C650 50 800 20 950 18 C1080 16 1150 40 1200 66" fill="none" stroke="#444" stroke-width="4"/>
  </svg>
  <div class="brand"><span class="brand-dot"></span><span class="brand-name">VINDGERDI</span></div>
  <nav class="nav"><a class="n1" href="#">Viðskiptaskilmálar</a><a class="n2" href="#">Spurt &amp; Svarað</a><a class="n3" href="#">Um Vindgerdi</a></nav>
  <h1 class="headline">Sama Rafmagn<br>Bara Ódýrara!</h1>
</header>

<main class="cards">
  <section class="card">
    <div class="icon-ring"><div class="icon-disc">
      <svg width="44" height="64" viewBox="0 0 44 64" fill="none" stroke="#7c9a02" stroke-width="3"><path d="M12 2v12M32 2v12M4 14h36v12c0 10-8 16-18 16S4 36 4 26z"/><path d="M24 20l-5 7h6l-5 7"/><path d="M22 42v8c0 6 6 8 12 8"/></svg>
    </div></div>
    <h2 class="card-title">Velkomin Í Viðskipti</h2>
    <p class="card-text">Lorem ipsum dolor sit a consectetuer adipiscing elit, sed diam nonummy nibh euismod tincidunt ut laoreet dolore magna aliquam erat volutpat.Ut wisi enim ad minim veniam quis.</p>
    <div class="btns"><a class="btn" href="#">FYRIRTÆKI</a><a class="btn alt" href="#">HEIMILI</a></div>
  </section>
  <section class="card">
    <div class="icon-ring"><div class="icon-disc">
      <svg width="50" height="62" viewBox="0 0 50 62" fill="none" stroke="#7c9a02" stroke-width="3"><path d="M2 2h38l8 8v50H2z"/><path d="M10 12h8M30 12h8M24 8v10M10 24h28M10 32h6v6h-6zM22 34h18M10 44h6v6h-6zM22 46h18"/></svg>
    </div></div>
    <h2 class="card-title">Verðskrá</h2>
    <div class="prices">
      <div class="price"><b>6.95</b>krónur / kWst</div>
      <div class="price"><b>6.22</b>krónur / kWst<br>rafmagnskynding</div>
    </div>
    <p class="compare">Gerðu verðsamanburð</p>
    <div class="btns"><a class="btn" href="#">VERÐVAKT</a></div>
  </section>
  <section class="card">
    <div class="icon-ring"><div class="icon-disc">
      <svg width="48" height="76" viewBox="0 0 48 76" fill="none" stroke="#7c9a02" stroke-width="4" stroke-linejoin="round"><path d="M30 2L4 44h20l-6 30L44 30H24z"/></svg>
    </div></div>
    <h2 class="card-title">Framtíðin Er Spennandi</h2>
    <p class="card-text">Gerum raforkukerfið snallara saman. Vindgerdi notar gervigreind, gagnavísindi og sjálfvirkni til að lágmarka kostnað og stuðla að okrujöfnuði</p>
    <div class="btns"><a class="btn" href="#">VITA MEIRA</a></div>
  </section>
</main>

<footer class="footer">
  <div class="contact" style="left:141px;top:36px">
    <span class="contact-icon"><svg width="22" height="18" viewBox="0 0 22 18" fill="none" stroke="#fff" stroke-width="1.5"><rect x="1" y="1" width="20" height="16"/><path d="M1 1l10 9 10-9"/></svg></span>
    <div class="contact-text">vindgerdi@vindgerdi-example.is<br>400-1234</div>
  </div>
  <div class="footer-mark"></div>
  <div class="contact" style="left:793px;top:36px">
    <span class="contact-icon"><svg width="16" height="22" viewBox="0 0 16 22" fill="none" stroke="#fff" stroke-width="1.5"><path d="M8 21C3 14 1 11 1 8a7 7 0 0114 0c0 3-2 6-7 13z"/><circle cx="8" cy="8" r="2.5"/></svg></span>
    <div class="contact-text"><div class="contact-head">HEIMILISFANG</div>Hafnargötu 8 220 Hafnarfirði</div>
  </div>
  <div class="company">Vindgerdi ehf<br>Kennitala: 510321-0270 &nbsp;&nbsp;·&nbsp;&nbsp; Vskm Númer: 142037</div>
</footer>
<div class="copyright">Copyright © Vindgerdi 2021 Allur Réttur Áskilin</div>
</body>
</html>
```